Musical download and streaming website

hello designers, I want to start up a musical website where users can download and rate music of different genres such as RnB, Hip hop, rock, afro-pop. This website should be attractive and contemporary. There will be a search column for different songs. Music files will be mp3, mwa, and others. I like blue, gold, pink and indigo colors. My website should resemble http://tunovalt.com. There should be good imaginary of music stars on my website.

```html
<!DOCTYPE html>
<html lang="en">
<head>
<meta charset="utf-8">
<title>Cadence Vault</title>
<link href="https://fonts.googleapis.com/css2?family=PT+Sans:wght@400;700&display=swap" rel="stylesheet">
<style>
:root{
  --yellow:#fde264;
  --yellow-light:#ffee8c;
  --yellow-line:#e9c94f;
  --blue:#34acd5;
  --blue-btn:#3aa3cc;
  --blue-deep:#2a86a6;
  --ink:#2b2b2b;
  --ink-soft:#444;
  --muted:#8a8a8a;
  --accent:#2ea7d3;
  --gold:#f1c63a;
  --star:#dcb300;
  --white:#fff;
}
*{box-sizing:border-box;margin:0;padding:0}
html,body{width:1200px;height:1083px;overflow:hidden}
body{font-family:"PT Sans",sans-serif;background:var(--blue);color:var(--ink);position:relative}
.hero{position:absolute;left:0;top:0;width:1200px;height:322px;
  background:radial-gradient(ellipse 520px 300px at 600px 130px,var(--yellow-light),var(--yellow) 75%)}
.wave{position:absolute;left:0;top:320px;width:1200px;height:60px}
.brand{position:absolute;top:38px;left:0;width:1200px;display:flex;justify-content:center;align-items:center;gap:12px}
.brand-dot{width:30px;height:30px;border-radius:50%;background:var(--ink)}
.brand-name{font-weight:700;font-size:30px;letter-spacing:2px;color:var(--ink);text-transform:uppercase}
.rule{position:absolute;left:131px;width:946px;height:1px;background:var(--yellow-line)}
.search{position:absolute;left:125px;top:137px;width:682px;height:63px;background:var(--white);border-radius:4px;
  border:1px solid #f0e2a0;padding:0 24px;display:flex;align-items:center;color:var(--muted);font-size:14px}
.search-btn{position:absolute;left:825px;top:137px;width:249px;height:63px;border-radius:4px;background:linear-gradient(#41b1d8,var(--blue-btn));
  color:var(--white);font-weight:700;font-size:21px;display:flex;align-items:center;justify-content:center;gap:6px}
.filters{position:absolute;left:128px;top:222px;width:948px;display:flex;justify-content:space-between;font-size:12.5px;color:var(--ink-soft)}
.filters ul{list-style:none;display:flex;gap:18px}
.filters li{display:flex;align-items:center;gap:4px}
.radio{width:11px;height:11px;border-radius:50%;background:linear-gradient(#fff,#ddd);border:1px solid #ccc}
.radio.on{background:radial-gradient(circle,#2a8fd8 35%,#fff 45%)}
.genres{gap:22px!important}
.listing{position:absolute;top:287px;left:0;width:1200px;text-align:center;font-size:12.5px;color:var(--ink-soft);word-spacing:4px}
.listing b{font-weight:400;letter-spacing:5.2px;margin-left:10px}
.section-title{position:absolute;left:111px;color:var(--white);font-weight:700;font-size:26px;letter-spacing:.5px}
.grid{position:absolute;left:111px;width:978px;display:grid;grid-template-columns:repeat(4,225px);column-gap:25px;row-gap:25px}
.card{height:87px;background:var(--white);border-radius:2px;display:flex;align-items:center;padding:0 14px;gap:13px}
.thumb{width:78px;height:55px;border-radius:3px;flex:none}
.card h3{font-weight:400;font-size:12.5px;color:var(--ink);margin-bottom:6px;white-space:nowrap}
.date{font-size:12.5px;color:var(--muted);display:flex;align-items:center;gap:3px}
.stars{display:flex;gap:1px}
.footer{position:absolute;left:0;top:915px;width:1200px;height:168px;background:var(--blue-deep);text-align:center;color:var(--white);font-size:12.5px}
.footer nav{margin-top:40px;word-spacing:2px}
.social{display:flex;justify-content:center;gap:6px;margin:16px 0 13px}
.social span{width:29px;height:29px;border-radius:50%;background:var(--gold)}
</style>
</head>
<body>
<header class="hero">
  <div class="brand"><span class="brand-dot"></span><span class="brand-name">Cadence Vault</span></div>
  <div class="rule" style="top:110px"></div>
  <div class="search">Search Text Here...</div>
  <div class="search-btn">
    <svg width="20" height="20" viewBox="0 0 20 20"><circle cx="8" cy="8" r="6" fill="none" stroke="#fff" stroke-width="2.6"/><line x1="12.5" y1="12.5" x2="18" y2="18" stroke="#fff" stroke-width="3" stroke-linecap="round"/></svg>SEARCH
  </div>
  <div class="filters">
    <ul>
      <li><span class="radio on"></span>All</li>
      <li><span class="radio"></span>Top Rated</li>
      <li><span class="radio"></span>Song</li>
      <li><span class="radio"></span>Artist</li>
    </ul>
    <ul class="genres">
      <li>Select Genres&nbsp;&nbsp;&nbsp;:</li>
      <li>RnB</li><li>Hip hop</li><li>Rock</li><li>Afro-pop</li>
    </ul>
  </div>
  <div class="rule" style="top:265px"></div>
  <p class="listing">Song Listing &nbsp;: <b>A B C D E F G H I J K L M N O P Q R S T U V W X Y Z</b></p>
</header>
<svg class="wave" viewBox="0 0 1200 60" preserveAspectRatio="none">
  <path d="M0 0H1200V27C1100 20 950 38 814 31C700 25 600 13 514 13C420 13 350 53 257 53C150 53 60 12 0 14Z" fill="#fde264" stroke="#e7c64a" stroke-width="1.5"/>
</svg>

<h2 class="section-title" style="top:412px">LAST ADDED</h2>
<section class="grid" style="top:475px" aria-label="Last added">
  <article class="card"><div class="thumb" role="img" aria-label="Hands playing guitar" style="background:linear-gradient(120deg,#1a1a22,#6b5a4a 60%,#222)"></div><div><h3>Lorem ipsum dolor</h3><p class="date"><svg width="12" height="12" viewBox="0 0 12 12"><rect x="1" y="2" width="10" height="9" fill="none" stroke="#2ea7d3" stroke-width="1.4"/><line x1="1" y1="5" x2="11" y2="5" stroke="#2ea7d3" stroke-width="1.4"/></svg>29 Jun 2016</p></div></article>
  <article class="card"><div class="thumb" role="img" aria-label="Sheet music pages" style="background:linear-gradient(120deg,#d9a860,#f3d9a3 50%,#b97c35)"></div><div><h3>Vivamus mollis qu</h3><p class="date"><svg width="12" height="12" viewBox="0 0 12 12"><rect x="1" y="2" width="10" height="9" fill="none" stroke="#2ea7d3" stroke-width="1.4"/><line x1="1" y1="5" x2="11" y2="5" stroke="#2ea7d3" stroke-width="1.4"/></svg>29 Jun 2016</p></div></article>
  <article class="card"><div class="thumb" role="img" aria-label="Fingers with music notes" style="background:linear-gradient(120deg,#7f8c99,#d4dce4 55%,#9aa6b2)"></div><div><h3>Fusce ligula ante</h3><p class="date"><svg width="12" height="12" viewBox="0 0 12 12"><rect x="1" y="2" width="10" height="9" fill="none" stroke="#2ea7d3" stroke-width="1.4"/><line x1="1" y1="5" x2="11" y2="5" stroke="#2ea7d3" stroke-width="1.4"/></svg>29 Jun 2016</p></div></article>
  <article class="card"><div class="thumb" role="img" aria-label="Street guitarist" style="background:linear-gradient(120deg,#c9c2b4,#8a7a64 55%,#5a5249)"></div><div><h3>Quisque non hend</h3><p class="date"><svg width="12" height="12" viewBox="0 0 12 12"><rect x="1" y="2" width="10" height="9" fill="none" stroke="#2ea7d3" stroke-width="1.4"/><line x1="1" y1="5" x2="11" y2="5" stroke="#2ea7d3" stroke-width="1.4"/></svg>29 Jun 2016</p></div></article>
  <article class="card"><div class="thumb" role="img" aria-label="Vinyl record and sleeves" style="background:linear-gradient(90deg,#1b1b1b,#333 40%,#9a4b4b 55%,#5a6b8a 75%,#c9a27a)"></div><div><h3>Duis mollis ex</h3><p class="date"><svg width="12" height="12" viewBox="0 0 12 12"><rect x="1" y="2" width="10" height="9" fill="none" stroke="#2ea7d3" stroke-width="1.4"/><line x1="1" y1="5" x2="11" y2="5" stroke="#2ea7d3" stroke-width="1.4"/></svg>29 Jun 2016</p></div></article>
  <article class="card"><div class="thumb" role="img" aria-label="Listener lying in a flower field" style="background:linear-gradient(120deg,#5c7a2c,#b89a4a 50%,#3f5e2a)"></div><div><h3>Donec purus neque</h3><p class="date"><svg width="12" height="12" viewBox="0 0 12 12"><rect x="1" y="2" width="10" height="9" fill="none" stroke="#2ea7d3" stroke-width="1.4"/><line x1="1" y1="5" x2="11" y2="5" stroke="#2ea7d3" stroke-width="1.4"/></svg>29 Jun 2016</p></div></article>
  <article class="card"><div class="thumb" role="img" aria-label="Concert crowd under stage lights" style="background:linear-gradient(180deg,#2a8a7a,#9fe0d0 35%,#0f1f22 75%)"></div><div><h3>Aliquam id tincidun</h3><p class="date"><svg width="12" height="12" viewBox="0 0 12 12"><rect x="1" y="2" width="10" height="9" fill="none" stroke="#2ea7d3" stroke-width="1.4"/><line x1="1" y1="5" x2="11" y2="5" stroke="#2ea7d3" stroke-width="1.4"/></svg>29 Jun 2016</p></div></article>
  <article class="card"><div class="thumb" role="img" aria-label="Recording studio equipment" style="background:linear-gradient(120deg,#1e2a38,#5a6a7a 50%,#c98a3a)"></div><div><h3>Lorem ipsum dolor</h3><p class="date"><svg width="12" height="12" viewBox="0 0 12 12"><rect x="1" y="2" width="10" height="9" fill="none" stroke="#2ea7d3" stroke-width="1.4"/><line x1="1" y1="5" x2="11" y2="5" stroke="#2ea7d3" stroke-width="1.4"/></svg>29 Jun 2016</p></div></article>
</section>

<h2 class="section-title" style="top:714px">TOP RATED</h2>
<section class="grid" style="top:777px" aria-label="Top rated">
  <article class="card"><div class="thumb" role="img" aria-label="Phone with red headphones" style="background:linear-gradient(120deg,#2a2a2a,#4a1a1a 50%,#1e1e1e)"></div><div><h3>Lorem ipsum dolor</h3><div class="stars"><svg width="78" height="14" viewBox="0 0 78 14"><defs><polygon id="s" points="7,0.5 8.9,5 13.5,5.2 9.9,8.1 11.1,13 7,10.3 2.9,13 4.1,8.1 0.5,5.2 5.1,5" fill="#dcb300"/></defs><use href="#s"/><use href="#s" x="15"/><use href="#s" x="30"/><use href="#s" x="45"/><polygon points="67,0.5 68.9,5 73.5,5.2 69.9,8.1 71.1,13 67,10.3 62.9,13 64.1,8.1 60.5,5.2 65.1,5" fill="none" stroke="#dcb300" stroke-width="1.3"/><polygon points="67,0.5 65.1,5 60.5,5.2 64.1,8.1 62.9,13 67,10.3" fill="#dcb300"/></svg></div></div></article>
  <article class="card"><div class="thumb" role="img" aria-label="Guitar on wooden floor" style="background:linear-gradient(90deg,#1e2a4a,#5a3a24 40%,#3a2416)"></div><div><h3>Lorem ipsum dolor</h3><div class="stars"><svg width="78" height="14" viewBox="0 0 78 14"><use href="#s"/><use href="#s" x="15"/><use href="#s" x="30"/><use href="#s" x="45"/><polygon points="67,0.5 68.9,5 73.5,5.2 69.9,8.1 71.1,13 67,10.3 62.9,13 64.1,8.1 60.5,5.2 65.1,5" fill="none" stroke="#dcb300" stroke-width="1.3"/><polygon points="67,0.5 65.1,5 60.5,5.2 64.1,8.1 62.9,13 67,10.3" fill="#dcb300"/></svg></div></div></article>
  <article class="card"><div class="thumb" role="img" aria-label="Piano keys" style="background:linear-gradient(180deg,#1a1408,#6a5220 45%,#e8e4dc 62%,#1a1a1a)"></div><div><h3>Lorem ipsum dolor</h3><div class="stars"><svg width="78" height="14" viewBox="0 0 78 14"><use href="#s"/><use href="#s" x="15"/><use href="#s" x="30"/><use href="#s" x="45"/><polygon points="67,0.5 68.9,5 73.5,5.2 69.9,8.1 71.1,13 67,10.3 62.9,13 64.1,8.1 60.5,5.2 65.1,5" fill="none" stroke="#dcb300" stroke-width="1.3"/><polygon points="67,0.5 65.1,5 60.5,5.2 64.1,8.1 62.9,13 67,10.3" fill="#dcb300"/></svg></div></div></article>
  <article class="card"><div class="thumb" role="img" aria-label="Child playing guitar" style="background:linear-gradient(120deg,#e8a36a,#c0703a 50%,#6a4a3a)"></div><div><h3>Lorem ipsum dolor</h3><div class="stars"><svg width="78" height="14" viewBox="0 0 78 14"><use href="#s"/><use href="#s" x="15"/><use href="#s" x="30"/><use href="#s" x="45"/><polygon points="67,0.5 68.9,5 73.5,5.2 69.9,8.1 71.1,13 67,10.3 62.9,13 64.1,8.1 60.5,5.2 65.1,5" fill="none" stroke="#dcb300" stroke-width="1.3"/><polygon points="67,0.5 65.1,5 60.5,5.2 64.1,8.1 62.9,13 67,10.3" fill="#dcb300"/></svg></div></div></article>
</section>

<footer class="footer">
  <nav>Home &nbsp;/&nbsp; About &nbsp;/&nbsp; Privacy Policy &nbsp;/&nbsp; Sitemap &nbsp;/&nbsp; Services</nav>
  <div class="social"><span></span><span></span><span></span><span></span></div>
  <p>@2016 Cadence Vault. All Rights Reserved.</p>
</footer>
</body>
</html>
```